I need a clean and unique business card

On one side I want it will have the company name and logo with the text underneath "The new standard"
The other side will have my contact information:
Tobias Rennet
Visionary & Founder
tobias.rennet@pelvorhealth.com
1.800.555.0147
The logo can get grayed out in a rotated angle.
Use your creativity for other examples

Business

```html
<!DOCTYPE html>
<html lang="en">
<head>
<meta charset="utf-8">
<title>Pelvor Health – Business Card</title>
<link href="https://fonts.googleapis.com/css2?family=Quicksand:wght@500;600;700&display=swap" rel="stylesheet">
<style>
  :root {
    --backdrop: #2b2b2d;
    --card-white: #ffffff;
    --card-black: #0a0b0c;
    --ink: #1e2b36;
    --muted: #6b7680;
    --accent-teal: #2bb99a;
    --accent-blue: #2f74b8;
    --text-light: #e9eef0;
    --shadow: rgba(0, 0, 0, 0.45);
  }
  html, body {
    margin: 0;
    width: 1200px;
    height: 900px;
    overflow: hidden;
    background: var(--backdrop);
    font-family: "Quicksand", sans-serif;
  }
  .canvas {
    position: relative;
    width: 1200px;
    height: 900px;
  }
  .card {
    position: absolute;
    width: 560px;
    height: 320px;
    border-radius: 22px;
    box-shadow: 0 14px 30px var(--shadow);
    box-sizing: border-box;
  }
  .card-front {
    left: 70px;
    top: 110px;
    background: var(--card-white);
    display: flex;
    flex-direction: column;
    align-items: center;
    justify-content: center;
  }
  .company-row {
    display: flex;
    align-items: center;
    gap: 14px;
  }
  .company-dot {
    width: 22px;
    height: 22px;
    border-radius: 50%;
    background: var(--ink);
  }
  .company-name {
    font-size: 44px;
    font-weight: 600;
    color: var(--ink);
  }
  .company-line {
    margin-top: 10px;
    font-size: 16px;
    font-weight: 500;
    color: var(--muted);
  }
  .card-back {
    left: 570px;
    top: 470px;
    background: var(--card-black);
    overflow: hidden;
    padding: 78px 0 0 44px;
    color: var(--text-light);
  }
  .back-accent {
    position: absolute;
    right: -40px;
    top: -40px;
    width: 280px;
    height: 280px;
    border-radius: 50%;
    background: radial-gradient(circle, rgba(43,185,154,0.16), rgba(47,116,184,0.05) 70%, transparent);
  }
  .person-name {
    margin: 0;
    font-size: 22px;
    font-weight: 600;
    color: var(--accent-teal);
    letter-spacing: 0.5px;
  }
  .person-title {
    margin: 2px 0 0;
    font-size: 15px;
    font-weight: 500;
  }
  .address {
    margin: 34px 0 12px;
    font-size: 14px;
    font-weight: 500;
    line-height: 1.45;
    font-style: normal;
  }
  .contact-list {
    list-style: none;
    margin: 0;
    padding: 0;
    font-size: 14px;
    font-weight: 500;
  }
  .contact-list li {
    display: flex;
    align-items: center;
    gap: 12px;
    margin-bottom: 7px;
  }
  .contact-icon {
    width: 15px;
    height: 15px;
    flex: none;
  }
</style>
</head>
<body>
<main class="canvas">
  <section class="card card-front" aria-label="Card front">
    <div class="company-row">
      <span class="company-dot" aria-hidden="true"></span>
      <span class="company-name">Pelvor Health</span>
    </div>
    <p class="company-line">The new standard</p>
  </section>

  <section class="card card-back" aria-label="Card back">
    <div class="back-accent" aria-hidden="true"></div>
    <h1 class="person-name">TOBIAS RENNET</h1>
    <p class="person-title">Visionary &amp; Founder</p>
    <address class="address">Northgate , 4120 Larkspur Ave,<br>Suite #12-40, Dallas, Texas 75219</address>
    <ul class="contact-list">
      <li>
        <svg class="contact-icon" viewBox="0 0 24 24" aria-hidden="true"><path fill="#2bb99a" d="M6.6 10.8a15.1 15.1 0 0 0 6.6 6.6l2.2-2.2a1 1 0 0 1 1-.25 11.4 11.4 0 0 0 3.6.57 1 1 0 0 1 1 1V20a1 1 0 0 1-1 1A17 17 0 0 1 3 4a1 1 0 0 1 1-1h3.5a1 1 0 0 1 1 1c0 1.25.2 2.45.57 3.57a1 1 0 0 1-.25 1z"/></svg>
        1.800.555.0147
      </li>
      <li>
        <svg class="contact-icon" viewBox="0 0 24 24" aria-hidden="true"><path fill="#2f74b8" d="M2 11 22 3l-8 20-3-9z"/></svg>
        tobias.rennet@pelvorhealth.com
      </li>
      <li>
        <svg class="contact-icon" viewBox="0 0 24 24" aria-hidden="true"><circle cx="12" cy="12" r="9" fill="none" stroke="#2f74b8" stroke-width="2.4"/><path d="M3 12h18M12 3c3 3 3 15 0 18M12 3c-3 3-3 15 0 18" fill="none" stroke="#2f74b8" stroke-width="1.6"/></svg>
        www.pelvorhealth.com
      </li>
    </ul>
  </section>
</main>
</body>
</html>
```